Stationery for a private security company, "Brenmoor Security Services Ltd."

Needed is a stationery design for a private security company. The designs must show professionalism and that our company mean nothing but business. Watermark of the company logo on the letterhead page is also a must. The final design must represent innovation and professionalism. It would be great if designers could integrate the colours black and silver onto the cards and letterheads..

Thank you

```html
<!DOCTYPE html>
<html lang="en">
<head>
<meta charset="utf-8">
<title>Brenmoor Security Services Ltd. — Stationery</title>
<link href="https://fonts.googleapis.com/css2?family=Open+Sans:wght@400;600&display=swap" rel="stylesheet">
<style>
  :root {
    --backdrop: #3b3b3b;
    --paper: #ffffff;
    --paper-shade: #ececec;
    --ink: #1e1e1e;
    --ink-soft: #555555;
    --rule: #8a8a8a;
    --band: #231f20;
    --silver: #c9c9c9;
    --watermark: #e4e4e4;
  }
  * { box-sizing: border-box; margin: 0; padding: 0; }
  html, body { width: 1200px; height: 779px; overflow: hidden; }
  body {
    position: relative;
    background: var(--backdrop);
    font-family: "Open Sans", sans-serif;
    color: var(--ink);
  }
  .sheet { position: absolute; overflow: hidden; }

  /* brand name set as text */
  .brand-name { font-weight: 600; color: var(--ink); line-height: 1.05; letter-spacing: 0.04em; }
  .brand-name .brand-main { display: block; text-transform: uppercase; }
  .brand-name .brand-sub { display: block; text-transform: uppercase; }

  .header-rule { position: absolute; height: 1px; background: var(--rule); }
  .tagline { position: absolute; font-size: 12px; color: var(--ink); white-space: nowrap; }

  /* letterhead */
  .letterhead {
    left: 73px; top: 52px; width: 478px; height: 675px;
    background: linear-gradient(160deg, var(--paper) 0%, var(--paper) 55%, var(--paper-shade) 100%);
  }
  .letterhead .brand-name { position: absolute; left: 40px; top: 42px; }
  .letterhead .brand-main { font-size: 17px; }
  .letterhead .brand-sub { font-size: 7px; }
  .letterhead .header-rule { left: 150px; right: 40px; top: 86px; }
  .letterhead .tagline { right: 40px; top: 64px; }
  .letterhead-watermark {
    position: absolute; left: 0; right: 0; top: 520px;
    text-align: center; font-weight: 600; color: var(--watermark);
    text-transform: uppercase; letter-spacing: 0.05em; line-height: 1.05;
  }
  .letterhead-watermark .brand-main { display: block; font-size: 52px; }
  .letterhead-watermark .brand-sub { display: block; font-size: 21px; }
  .letterhead-contact {
    position: absolute; left: 40px; right: 40px; top: 640px;
    display: flex; align-items: center; font-size: 7.5px; color: var(--ink);
  }
  .letterhead-contact span { padding: 0 14px; border-left: 1px solid var(--rule); }
  .letterhead-contact span:first-child { padding-left: 0; border-left: none; }
  .letterhead-band {
    position: absolute; left: 0; right: 0; bottom: 0; height: 16px; background: var(--band);
    color: var(--silver); font-size: 7px; letter-spacing: 0.9em; text-align: center; line-height: 16px;
  }
  .letterhead-strip {
    position: absolute; left: 73px; top: 711px; width: 478px; height: 16px; background: var(--band);
    color: var(--silver); font-size: 7px; letter-spacing: 0.9em; text-align: center; line-height: 16px;
  }

  /* business card */
  .card-front {
    left: 585px; top: 84px; width: 202px; height: 115px; background: var(--paper);
  }
  .card-front .brand-name { position: absolute; left: 12px; top: 20px; }
  .card-front .brand-main { font-size: 8.5px; }
  .card-front .brand-sub { font-size: 4px; }
  .card-front .header-rule { left: 64px; right: 10px; top: 40px; }
  .card-front .tagline { right: 10px; top: 29px; font-size: 7px; }
  .card-person { position: absolute; left: 12px; top: 68px; }
  .card-person-name { font-size: 6.5px; font-weight: 600; text-transform: uppercase; letter-spacing: 0.04em; }
  .card-person-role { font-size: 4px; color: var(--ink-soft); }
  .card-details {
    position: absolute; left: 12px; right: 10px; top: 86px;
    display: flex; justify-content: space-between; font-size: 4px; line-height: 1.5; color: var(--ink-soft);
  }
  .card-details .card-address { text-align: right; }
  .card-band {
    position: absolute; left: 0; right: 0; bottom: 0; height: 10px; background: var(--band);
    color: var(--silver); font-size: 5px; letter-spacing: 0.35em; padding-left: 12px; line-height: 10px;
  }
  .card-back {
    left: 799px; top: 84px; width: 192px; height: 115px; background: var(--band);
    display: flex; align-items: center; justify-content: center; text-align: center;
  }
  .card-back .brand-name { color: var(--silver); }
  .card-back .brand-main { font-size: 13px; }
  .card-back .brand-sub { font-size: 6px; }

  /* envelope front */
  .envelope-front {
    left: 584px; top: 231px; width: 549px; height: 236px;
    background: linear-gradient(180deg, var(--paper) 0%, var(--paper-shade) 100%);
  }
  .envelope-front .brand-name { position: absolute; left: 38px; top: 40px; }
  .envelope-front .brand-main { font-size: 15px; }
  .envelope-front .brand-sub { font-size: 6px; }
  .envelope-front .header-rule { left: 140px; right: 36px; top: 87px; }
  .envelope-front .tagline { right: 36px; top: 66px; font-size: 11.5px; }
  .envelope-band {
    position: absolute; left: 0; right: 0; bottom: 0; height: 16px; background: var(--band);
    color: var(--silver); font-size: 7px; text-align: center; line-height: 16px;
  }

  /* envelope back */
  .envelope-back {
    left: 584px; top: 488px; width: 549px; height: 239px;
    background: linear-gradient(180deg, var(--paper) 0%, var(--paper-shade) 100%);
  }
  .envelope-flap { position: absolute; left: 0; top: 0; width: 549px; height: 92px; }
  .envelope-web {
    position: absolute; left: 0; right: 0; top: 30px; text-align: center;
    font-size: 9.5px; color: var(--paper); letter-spacing: 0.02em;
  }
  .envelope-watermark {
    position: absolute; left: 0; right: 0; top: 160px; text-align: center; color: var(--watermark);
  }
  .envelope-watermark .brand-name { color: var(--watermark); }
  .envelope-watermark .brand-main { font-size: 15px; }
  .envelope-watermark .brand-sub { font-size: 6px; }
</style>
</head>
<body>

  <!-- Letterhead -->
  <section class="sheet letterhead" aria-label="Letterhead">
    <div class="brand-name">
      <span class="brand-main">Brenmoor</span>
      <span class="brand-sub">Security Services Ltd.</span>
    </div>
    <div class="header-rule"></div>
    <p class="tagline">A Tradition Of Trust</p>

    <div class="letterhead-watermark" aria-hidden="true">
      <span class="brand-main">Brenmoor</span>
      <span class="brand-sub">Security Services Ltd.</span>
    </div>

    <div class="letterhead-contact">
      <span>+00 987 654 32100</span>
      <span>sales@brenmoorsecurity.com</span>
      <span>your dummy address, dummy city, dummy zipcode</span>
    </div>
  </section>
  <div class="letterhead-strip">www.brenmoorsecurity.com</div>

  <!-- Business card front -->
  <section class="sheet card-front" aria-label="Business card front">
    <div class="brand-name">
      <span class="brand-main">Brenmoor</span>
      <span class="brand-sub">Security Services Ltd.</span>
    </div>
    <div class="header-rule"></div>
    <p class="tagline">A Tradition Of Trust</p>
    <div class="card-person">
      <p class="card-person-name">Daniel Harrow</p>
      <p class="card-person-role">Director/ Founder</p>
    </div>
    <div class="card-details">
      <div class="card-contact">+00 987 654 32100<br>sales@brenmoorsecurity.com</div>
      <div class="card-address">your dummy address<br>dummy city, dummy zipcode</div>
    </div>
    <div class="card-band">www.brenmoorsecurity.com</div>
  </section>

  <!-- Business card back -->
  <section class="sheet card-back" aria-label="Business card back">
    <div class="brand-name">
      <span class="brand-main">Brenmoor</span>
      <span class="brand-sub">Security Services Ltd.</span>
    </div>
  </section>

  <!-- Envelope front -->
  <section class="sheet envelope-front" aria-label="Envelope front">
    <div class="brand-name">
      <span class="brand-main">Brenmoor</span>
      <span class="brand-sub">Security Services Ltd.</span>
    </div>
    <div class="header-rule"></div>
    <p class="tagline">A Tradition Of Trust</p>
    <div class="envelope-band">your dummy address, dummy city, dummy zipcode</div>
  </section>

  <!-- Envelope back -->
  <section class="sheet envelope-back" aria-label="Envelope back">
    <svg class="envelope-flap" viewBox="0 0 549 92" aria-hidden="true">
      <path d="M0 0 H549 L536 34 Q531 46 514 49 L290 88 Q274 91 258 88 L35 49 Q18 46 13 34 Z" fill="var(--band)"/>
    </svg>
    <p class="envelope-web">www.brenmoorsecurity.com</p>
    <div class="envelope-watermark" aria-hidden="true">
      <div class="brand-name">
        <span class="brand-main">Brenmoor</span>
        <span class="brand-sub">Security Services Ltd.</span>
      </div>
    </div>
  </section>

</body>
</html>
```